PitchTally Webpages and Logo

See attached brief. Take the existing website www.pitchtally.co.uk and logo and transform these assets to:

Give people who arrive on the site for first time the confidence to sign-up easily and quickly
Allow regular returning users quick and easy placing of predictions and encourage them to share the PitchTally prediction on social networks and with their contacts
Convey the essence of a community working together to enjoyably come-up with smart predictions on sporting events
Work seamlessly and well across smartphones, tablets and desktop i.e. Should be Responsive Web Design
Updates

Target Market(s)

Users are sports fans with opinions
Primarily male and early twenties to mid-thirties
They are competitive - they want to beat their peers
Many are from outside the UK

Industry/Entity Type

Events

Logo Text

PitchTally

Coding

Coded - Design and coding required

Number of Pages Required

4 page

Font styles to use
Sans Serif

Requirements
Must have
• Responsive Web Design
• Mobile First
• HTML must work with dedicated bespoke application developed in ASP.NET using MS SQL underneath
• See Brief
Nice to have
• See brief
Should not have
• See brief

```html
<!DOCTYPE html>
<html lang="en">
<head>
<meta charset="utf-8">
<title>PitchTally</title>
<link rel="stylesheet" href="https://fonts.googleapis.com/css2?family=Arimo:wght@400;700&family=Open+Sans:wght@400;600&display=swap">
<style>
:root{
  --green:#8dc21f;
  --green-dark:#6f9f12;
  --blue:#2aa6e0;
  --ink:#555;
  --muted:#888;
  --line:#e3e3e3;
  --band:#f4f4f4;
  --footer:#575757;
}
*{box-sizing:border-box;margin:0;padding:0}
html,body{width:898px;height:1200px;overflow:hidden;background:#fff;font-family:"Arimo",sans-serif;color:var(--ink)}
.page{position:relative;width:898px;height:1200px}
.top-rule{position:absolute;top:0;left:0;width:100%;height:2px;background:var(--green)}
.brand{position:absolute;left:74px;top:14px;display:flex;flex-direction:column;align-items:center}
.brand-mark{width:30px;height:30px;border-radius:50%;background:var(--blue);margin-bottom:8px}
.brand-name{font-size:16px;font-weight:700;color:#555;letter-spacing:.3px}
.nav{position:absolute;top:37px;left:312px;display:flex;align-items:center}
.nav a{font-size:10px;color:#666;text-decoration:none;margin-right:30px;line-height:23px}
.nav .btn{margin-right:6px;color:#fff;width:66px;text-align:center;height:23px;border-radius:2px}
.btn-login{background:var(--blue);margin-left:-8px}
.btn-register{background:var(--green)}
.hero{position:absolute;top:94px;left:0;width:898px;height:371px;overflow:hidden}
.hero-photo{position:absolute;inset:0;background:
  linear-gradient(90deg,rgba(0,0,0,0) 0%,rgba(0,0,0,0) 55%,rgba(90,35,40,.45) 100%),
  linear-gradient(180deg,#3b4a5d 0%,#7a6650 33%,#4a3e38 55%,#2f3a2c 80%,#2c3a26 100%)}
.hero-title{position:absolute;left:94px;top:112px;font-size:46px;font-weight:700;color:#fff;letter-spacing:.5px}
.hero-copy{position:absolute;left:100px;top:170px;width:385px;font-size:10px;line-height:18.6px;color:#fff}
.join{position:absolute;left:102px;top:243px;width:139px;height:33px;background:linear-gradient(#a9d532,#7fb31a);border-radius:2px;color:#3f5e08;font-weight:700;font-size:15px;text-align:center;line-height:33px}
.dots{position:absolute;left:88px;top:348px;display:flex;gap:5px}
.dots i{width:8px;height:8px;border-radius:50%;background:var(--blue);border:1px solid #fff}
.dots i.on{background:var(--green)}
.features{position:absolute;top:495px;left:0;width:898px}
.feature{position:absolute;width:220px;text-align:center}
.feature-icon{width:86px;height:86px;margin:0 auto;border-radius:50%;border:4px solid #ececec;background:#f2f2f2;display:flex;align-items:center;justify-content:center}
.feature h3{margin-top:14px;font-size:14px;color:#666;font-weight:700}
.feature p{margin-top:6px;font-size:7.5px;line-height:15.5px;color:var(--muted)}
.fixtures{position:absolute;top:682px;left:0;width:898px;height:209px;background:var(--band);border-top:1px solid #eaeaea;border-bottom:1px solid #eaeaea}
.fixture-card{position:absolute;top:19px;width:236px;height:159px;border:1px solid var(--line);background:var(--band)}
.match{position:absolute;left:0;width:100%;height:70px}
.team{position:absolute;width:80px;text-align:center}
.badge{width:36px;height:36px;margin:0 auto 8px;border-radius:4px}
.team span{font-size:7.5px;color:#666}
.vs{position:absolute;left:110px;top:14px;font-size:12px;color:#888}
.testimonials{position:absolute;top:926px;left:0;width:898px}
.quote-card{position:absolute;width:355px;height:111px;border:1px solid var(--line);background:#fff;box-shadow:0 1px 2px rgba(0,0,0,.06)}
.avatar{position:absolute;left:14px;top:14px;width:56px;height:56px;border-radius:50%;border:3px solid #f0f0f0}
.quote-name{position:absolute;left:80px;top:20px;width:262px;padding-bottom:7px;border-bottom:1px solid #eee;font-family:"Open Sans",sans-serif;font-size:8px;color:var(--blue)}
.quote-text{position:absolute;left:83px;top:42px;width:262px;font-family:"Open Sans",sans-serif;font-size:7.5px;line-height:15px;color:var(--muted)}
.quote-text b{font-size:14px;color:#bbb;vertical-align:-3px;margin-right:4px}
.quote-close{position:absolute;left:175px;top:86px;font-size:14px;color:#bbb;font-weight:700}
.partners{position:absolute;top:1070px;left:100px;width:700px;display:flex;justify-content:space-between;align-items:center}
.partners span{font-size:20px;color:#9a9a9a;font-weight:400}
.footer{position:absolute;top:1143px;left:0;width:898px;height:57px;background:var(--footer)}
.copyright{position:absolute;left:75px;top:24px;font-size:8px;color:#fff}
.social{position:absolute;left:689px;top:18px;display:flex;gap:6px}
.social i{width:22px;height:22px;border-radius:50%;border:1.5px solid #ddd}
</style>
</head>
<body>
<div class="page">
  <div class="top-rule"></div>
  <header>
    <div class="brand"><span class="brand-mark"></span><span class="brand-name">PITCHTALLY</span></div>
    <nav class="nav">
      <a href="#">HOME</a><a href="#">MINILIGA</a><a href="#">TABLES</a><a href="#">KITTY</a><a href="#">FAQ</a><a href="#">ME</a>
      <a href="#" class="btn btn-login">LOGIN</a><a href="#" class="btn btn-register">REGISTER</a>
    </nav>
  </header>

  <section class="hero">
    <div class="hero-photo" role="img" aria-label="Photo of a stadium at dusk with a football player on the right"></div>
    <h1 class="hero-title">PITCHTALLY</h1>
    <p class="hero-copy">It is a long established fact that a reader will be distracted by the readable content of page when looking at its layout. The point of using Lorem Ipsum is that it has a more-or-less normal distribu making it look like readable English.</p>
    <div class="join">JOIN NOW</div>
    <div class="dots"><i></i><i class="on"></i><i></i><i></i></div>
  </section>

  <section class="features">
    <div class="feature" style="left:81px">
      <div class="feature-icon"><svg width="22" height="22" viewBox="0 0 24 24"><path fill="#777" d="M2 10h4v12H2zM8 22V10l5-8c2 0 3 1 2.5 3L14 9h6c1.5 0 2.5 1.3 2 2.7l-2.5 8.5c-.3 1-1.2 1.8-2.3 1.8z"/></svg></div>
      <h3>RESULT</h3>
      <p>It is a long established fact that a reader will be distracted by<br>the here making it look like readable English.</p>
    </div>
    <div class="feature" style="left:343px">
      <div class="feature-icon"><svg width="22" height="22" viewBox="0 0 24 24"><path fill="#777" d="M12 1l3.3 7 7.7.8-5.8 5.2 1.7 7.6L12 17.7 5.1 21.6l1.7-7.6L1 8.8 8.7 8z"/></svg></div>
      <h3>SCORE</h3>
      <p>It is a long established fact that a reader will be distracted by<br>the here making it look like readable English.</p>
    </div>
    <div class="feature" style="left:594px">
      <div class="feature-icon"><svg width="22" height="22" viewBox="0 0 24 24"><path fill="none" stroke="#777" stroke-width="2" d="M7 3h10v6a5 5 0 0 1-10 0zM7 5H3c0 4 2 5 4 5M17 5h4c0 4-2 5-4 5M12 14v4M8 21h8M9 18h6"/></svg></div>
      <h3>GOAL</h3>
      <p>It is a long established fact that a reader will be distracted by<br>the here making it look like readable English.</p>
    </div>
  </section>

  <section class="fixtures">
    <div class="fixture-card" style="left:74px">
      <div class="match" style="top:13px">
        <div class="team" style="left:0"><div class="badge" style="background:#9bbfdd"></div><span>Northgate City</span></div>
        <div class="vs">V</div>
        <div class="team" style="left:136px"><div class="badge" style="background:#c8485a"></div><span>Harbour Rovers</span></div>
      </div>
      <div class="match" style="top:91px">
        <div class="team" style="left:0"><div class="badge" style="background:#8f5a78"></div><span>Northgate City</span></div>
        <div class="vs">V</div>
        <div class="team" style="left:136px"><div class="badge" style="background:#d44a3a"></div><span>Harbour Rovers</span></div>
      </div>
    </div>
    <div class="fixture-card" style="left:332px">
      <div class="match" style="top:13px">
        <div class="team" style="left:0"><div class="badge" style="background:#4a66a8"></div><span>Northgate City</span></div>
        <div class="vs">V</div>
        <div class="team" style="left:136px"><div class="badge" style="background:#3a4e80"></div><span>Harbour Rovers</span></div>
      </div>
      <div class="match" style="top:91px">
        <div class="team" style="left:0"><div class="badge" style="background:#3a4a70"></div><span>Northgate City</span></div>
        <div class="vs">V</div>
        <div class="team" style="left:136px"><div class="badge" style="background:#c9c870"></div><span>Harbour Rovers</span></div>
      </div>
    </div>
    <div class="fixture-card" style="left:588px">
      <div class="match" style="top:13px">
        <div class="team" style="left:0"><div class="badge" style="background:#8a4a55"></div><span>Northgate City</span></div>
        <div class="vs">V</div>
        <div class="team" style="left:136px"><div class="badge" style="background:#3f62a8"></div><span>Harbour Rovers</span></div>
      </div>
      <div class="match" style="top:91px">
        <div class="team" style="left:0"><div class="badge" style="background:#8f5a78"></div><span>Northgate City</span></div>
        <div class="vs">V</div>
        <div class="team" style="left:136px"><div class="badge" style="background:#d44a3a"></div><span>Harbour Rovers</span></div>
      </div>
    </div>
  </section>

  <section class="testimonials">
    <article class="quote-card" style="left:75px">
      <div class="avatar" role="img" aria-label="Portrait photo of a customer" style="background:linear-gradient(135deg,#e9c9a8,#c98a5c)"></div>
      <div class="quote-name">Jhon Smith , City Name</div>
      <p class="quote-text"><b>“</b>vero eos et accusamus et iusto odio dignissimos ducimus  qui blanditiis praesentium voluptatum deleniti atque corr upti quos dolores et quas molestias excepturi sint occaecati cupiditate non provident.</p>
      <div class="quote-close">”</div>
    </article>
    <article class="quote-card" style="left:469px">
      <div class="avatar" role="img" aria-label="Portrait photo of a customer" style="background:linear-gradient(135deg,#6a5a52,#2e2a2a)"></div>
      <div class="quote-name">Jhon Smith , City Name</div>
      <p class="quote-text"><b>“</b>vero eos et accusamus et iusto odio dignissimos ducimus  qui blanditiis praesentium voluptatum deleniti atque corr upti quos dolores et quas molestias excepturi sint occaecati cupiditate non provident.</p>
      <div class="quote-close">”</div>
    </article>
  </section>

  <section class="partners">
    <span>brightmark</span><span>PageForge</span><span>taskhive</span><span>scriptly</span><span>Cartwell</span><span>Polyform</span>
  </section>

  <footer class="footer">
    <p class="copyright">© Copyright  2014 Vexa Digital.All rights are reserved</p>
    <div class="social"><i></i><i></i><i></i><i></i><i></i></div>
  </footer>
</div>
</body>
</html>
```